Australian Trucking Company Requires Professional Looking Stationary

We require a professional looking stationary design that incorporates our newly designed logo.

Our business, called "Brell Haulage Contracting", provides contracting work, transport and logistics to business in Western Australia particularly with links to the mining sector.

We are a small business looking to expand and our new logo and our new stationary will help develop our brand image in our market place.

Target Market(s)

Businesses and Corporation with links to the Mining Sector

Industry/Entity Type

Small Business

Requirements
Must have
• The letterhead must have the following details:
The new logo

Text saying: "Brell Holdings Pty Ltd (ACN 582 316 907) ATF The Brell Discretionary Trust T/AS"
"ABN 71 834 209 553"
Address "P.O Box 817 Wattlegrove WA, 6958"
Phone: 08 9352 7140
Email: brellhaul@mailbox-example.com.au

The text on the letterhead should be editable as the details are likely to change in the near future. Provision should be made for a website address all though one isn't available at the moment.

The styling, layout and font text is entirely up to the designer.

```html
<!DOCTYPE html>
<html lang="en">
<head>
<meta charset="utf-8">
<title>Brell Haulage Contracting – Business Card</title>
<link rel="stylesheet" href="https://fonts.googleapis.com/css2?family=Open+Sans:wght@400;600;700;800&display=swap">
<style>
  :root {
    --backdrop: #e9e6e2;
    --card: #ffffff;
    --brand-red: #d41f26;
    --brand-red-deep: #a3141a;
    --swoosh-grey: #a9a9ab;
    --ink: #1e1e1e;
    --art-dark: #2a2a2a;
    --art-mid: #6d6d6d;
    --on-red: #ffffff;
  }
  * { box-sizing: border-box; margin: 0; padding: 0; }
  html, body { width: 1200px; height: 426px; overflow: hidden; }
  body {
    background: var(--backdrop);
    font-family: "Open Sans", Arial, sans-serif;
    color: var(--ink);
    position: relative;
  }
  .card {
    position: absolute;
    width: 543px;
    height: 295px;
    background: var(--card);
    border-radius: 18px;
    overflow: hidden;
    box-shadow: 0 4px 12px rgba(0,0,0,.18);
  }
  .card--front { left: 55px; top: 57px; }
  .card--back  { left: 610px; top: 62px; }

  .swoosh { position: absolute; inset: 0; width: 100%; height: 100%; }

  .truck-art {
    position: absolute;
    border-radius: 10px;
  }
  .truck-art--header {
    left: 27px; top: 26px; width: 112px; height: 86px;
    background: linear-gradient(160deg, var(--art-mid), var(--art-dark));
    opacity: .8;
  }
  .truck-art--swoosh {
    left: 262px; top: 146px; width: 78px; height: 70px;
    background: linear-gradient(160deg, #3a3a3a, #111);
  }
  .truck-art--hero {
    left: 180px; top: 40px; width: 300px; height: 222px;
    background: radial-gradient(ellipse at 55% 50%, #1a1a1a 0%, #222 60%, #444 100%);
    border-radius: 18px;
  }

  .brand-name {
    position: absolute;
    left: 158px; top: 34px;
    font-weight: 800;
    font-size: 30px;
    line-height: 30px;
    color: var(--brand-red);
    text-transform: uppercase;
    letter-spacing: .5px;
  }

  .contact-list {
    position: absolute;
    left: 28px; top: 140px;
    list-style: none;
    font-size: 12px;
  }
  .contact-list li { display: flex; align-items: center; gap: 6px; height: 17px; white-space: nowrap; }
  .contact-list li.address { margin-top: 16px; }
  .contact-list svg { width: 11px; height: 11px; fill: var(--brand-red); flex: none; }

  .legal {
    position: absolute;
    right: 45px; top: 234px;
    text-align: right;
    color: var(--on-red);
    font-size: 11.5px;
    line-height: 17px;
  }
  .legal .abn { margin-top: 3px; }

  .person {
    position: absolute;
    left: 30px; top: 260px;
    color: var(--on-red);
    font-weight: 700;
    font-size: 17px;
  }
  .person .role { font-weight: 400; font-size: 12.5px; }
</style>
</head>
<body>

<section class="card card--front" aria-label="Business card front">
  <svg class="swoosh" viewBox="0 0 543 295" preserveAspectRatio="none" aria-hidden="true">
    <defs>
      <linearGradient id="redBand" x1="0" y1="0" x2="0" y2="1">
        <stop offset="0" stop-color="var(--brand-red)"/>
        <stop offset="1" stop-color="var(--brand-red-deep)"/>
      </linearGradient>
    </defs>
    <path d="M0,234 Q270,228 543,84 L543,112 Q290,236 0,243 Z" fill="var(--swoosh-grey)"/>
    <path d="M0,248 Q300,244 543,124 L543,295 L0,295 Z" fill="url(#redBand)"/>
  </svg>

  <div class="truck-art truck-art--header" role="img" aria-label="Grey truck illustration"></div>
  <div class="brand-name">Brell<br>Haulage<br>Contracting</div>

  <ul class="contact-list">
    <li>
      <svg viewBox="0 0 24 24"><path d="M6.6 10.8a15 15 0 0 0 6.6 6.6l2.2-2.2c.3-.3.7-.4 1-.2 1.1.4 2.3.6 3.6.6.6 0 1 .4 1 1V20c0 .6-.4 1-1 1A17 17 0 0 1 3 4c0-.6.4-1 1-1h3.5c.6 0 1 .4 1 1 0 1.3.2 2.5.6 3.6.1.3 0 .7-.2 1z"/></svg>
      08 9352 7140
    </li>
    <li>
      <svg viewBox="0 0 24 24"><path d="M2 5h20v14H2z M4 7v.5l8 5 8-5V7z" fill-rule="evenodd"/></svg>
      brellhaul@mailbox-example.com.au
    </li>
    <li class="address">
      <svg viewBox="0 0 24 24"><path d="M12 3 2 12h3v8h5v-5h4v5h5v-8h3z"/></svg>
      P.O Box 817 Wattlegrove WA, 6958
    </li>
  </ul>

  <div class="truck-art truck-art--swoosh" role="img" aria-label="Black truck illustration"></div>

  <div class="legal">
    <p>Brell Holdings Pty Ltd (ACN 582 316 907)</p>
    <p>ATF The Brell Discretionary Trust T/AS</p>
    <p class="abn">ABN 71 834 209 553</p>
  </div>

  <p class="person">Persons name, <span class="role">Manager</span></p>
</section>

<section class="card card--back" aria-label="Business card back">
  <div class="truck-art truck-art--hero" role="img" aria-label="Large black truck illustration"></div>
</section>

</body>
</html>
```